PostCard Design Project

I am making a mailing postcard
I am having the mailing printed using 4 color foil on certain parts.
I am looking for a design that maximizes the foil process where certain parts are done in foil to grab the customers attention (example: if there is a car on the postcard the headlights would be done in foil) .
I am targeting some industries, (auto, real estate, medical, beauty) I would like the post card to have examples of postcard ideas for 2 or 3 of these industries.
specs:
the postcard should be atleast 6.5x9 up to 8.5x11, I don't want to restrict the space for the creative as I don't want everything to look like a huge mess. both sides will be used.
the piece is a direct mail piece so it has to meet requirements of https://www.mailvantor.com/business/pdf/quick-reference-guide.pdf
text will be
"business with no limits, meet mailing with no addresses, gain new customers through "Open Porch Route Drop" reach new customers at their home without needing their address. "
I also want some current print specials I am running included.
-double your order FREE (order 500 business cards and get 1000)
-250 100lb gloss stock brochures 99.00
-business packages (cards, envelopes and letterhead) 299
-1000 flyers 140.40
-5000 postcards 179.99
A list of services
banners
booklets
brochures
business cards
calendars
catalogs
CD/DVD packages
envelopes
event tickets
flyers
hangtags
postcards
posters
presentation folders
rack cards
labels
table tents
window cling and decal
"order 24/7 orders@inkwillow.com" must be included
my logo is InkWillow will be supplied later
ive received some great designs. however Im looking for something a little more modern like some zorvel would put out. if the amount of words is too much please feel free to edit. also an idea i had for the list of services i offer is to have it transparent yet readable as the background of the postcard some small some big but covering the entire backgroud. you can then design on top of that with other thing. just an early morning thought
Reason: I have uploaded a sketch of my idea, please take time to look at it for an accurate depiction of what im looking for. feel free to add elements that make it pop off the page
Reason: We are getting close i will be providing feed back today

```html
<!DOCTYPE html>
<html lang="en">
<head>
<meta charset="utf-8">
<title>InkWillow Postcard – Front and Back</title>
<link rel="stylesheet" href="https://fonts.googleapis.com/css2?family=Arimo:wght@400;700&family=Open+Sans:wght@400;600;700&display=swap">
<style>
  :root {
    --page: #e8e5e0;
    --navy: #0b2a3d;
    --deep: #0f4a6b;
    --sky: #2f9fd6;
    --sky-light: #4fb6e3;
    --quote-blue: #2f9be0;
    --yellow: #e8ee1c;
    --green: #3fae49;
    --band-blue: #2a8fd0;
    --black: #070707;
    --white: #ffffff;
    --label-bg: #1f2a31;
  }
  * { box-sizing: border-box; margin: 0; padding: 0; }
  html, body { width: 1200px; height: 900px; overflow: hidden; }
  body {
    background: var(--page);
    position: relative;
    font-family: "Open Sans", Arial, sans-serif;
  }
  .postcard {
    position: absolute;
    top: 263px;
    width: 560px;
    height: 373px;
    overflow: hidden;
    box-shadow: 0 6px 18px rgba(0,0,0,.25);
  }
  .postcard--front { left: 30px; }
  .postcard--back { left: 610px; }
  .postcard__art { position: absolute; inset: 0; width: 100%; height: 100%; }

  /* Front */
  .headline {
    position: absolute;
    left: 18px;
    top: 34px;
    width: 240px;
    font-family: "Arimo", Arial, sans-serif;
    font-weight: 700;
    font-size: 11.5px;
    line-height: 1.35;
    text-transform: uppercase;
    color: var(--quote-blue);
  }
  .headline__program { display: block; font-size: 17px; line-height: 1.25; margin: 2px 0; }
  .specials {
    position: absolute;
    left: 380px;
    top: 20px;
    width: 110px;
    list-style: none;
    color: var(--white);
    font-size: 9px;
    line-height: 1.4;
  }
  .specials li { padding-left: 12px; position: relative; }
  .specials li::before {
    content: "";
    position: absolute; left: 1px; top: 3px;
    width: 4px; height: 7px;
    border: solid var(--white); border-width: 0 2px 2px 0;
    transform: rotate(40deg);
  }
  .specials .note { padding-left: 12px; }
  .specials .note::before { display: none; }
  .logo-badge {
    position: absolute;
    left: 480px;
    top: 218px;
    width: 78px;
    text-align: center;
    font-family: "Open Sans", Arial, sans-serif;
    font-weight: 700;
    font-size: 15px;
    color: var(--band-blue);
  }
  .samples {
    position: absolute;
    left: 200px;
    top: 200px;
    width: 200px;
    height: 132px;
    background: linear-gradient(135deg, #f3f3f3 0%, #d94b4b 45%, #f0a43a 75%, #e9eef3 100%);
    opacity: .9;
  }
  .order-line {
    position: absolute;
    right: 22px;
    bottom: 9px;
    color: var(--sky-light);
    font-weight: 600;
    font-size: 15px;
    letter-spacing: .3px;
  }

  /* Back */
  .services-label {
    position: absolute;
    left: 30px;
    top: 34px;
    padding: 4px 12px;
    background: var(--label-bg);
    color: var(--white);
    font-size: 13px;
  }
  .services {
    position: absolute;
    list-style: none;
    color: var(--white);
    font-weight: 600;
    font-size: 14px;
    line-height: 1.75;
  }
  .services li { padding-left: 14px; position: relative; white-space: nowrap; }
  .services li::before {
    content: "";
    position: absolute; left: 1px; top: 7px;
    width: 4px; height: 8px;
    border: solid var(--white); border-width: 0 2px 2px 0;
    transform: rotate(40deg);
  }
  .services--first { left: 30px; top: 130px; }
  .services--second { left: 170px; top: 100px; }
  .services--third { left: 315px; top: 64px; line-height: 1.6; }
  .stamp-box {
    position: absolute;
    right: 20px;
    top: 18px;
    width: 70px;
    height: 50px;
    border: 1px solid #222;
    background: var(--white);
    color: #222;
    font-size: 9px;
    display: flex; align-items: center; justify-content: center;
    text-align: center;
    line-height: 1.2;
  }
  .postcard--back .order-line { color: var(--white); right: 18px; bottom: 14px; }
</style>
</head>
<body>

<section class="postcard postcard--front" aria-label="Postcard front">
  <svg class="postcard__art" viewBox="0 0 560 373" preserveAspectRatio="none" aria-hidden="true">
    <defs>
      <linearGradient id="front-sky" x1="0" y1="0" x2="0" y2="1">
        <stop offset="0" stop-color="#1b6d9a"/>
        <stop offset="1" stop-color="#2f9fd6"/>
      </linearGradient>
    </defs>
    <rect width="560" height="373" fill="url(#front-sky)"/>
    <path d="M0,0 H376 C345,170 245,315 0,373 Z" fill="#1d5f86"/>
    <path d="M0,0 H360 C330,165 233,305 0,366 Z" fill="#2a8fd0"/>
    <path d="M0,0 H348 C318,160 223,298 0,360 Z" fill="#3fae49"/>
    <path d="M0,0 H336 C306,155 213,292 0,352 Z" fill="#e8ee1c"/>
    <path d="M0,0 H322 C292,150 201,284 0,344 Z" fill="#070707"/>
    <circle cx="580" cy="230" r="118" fill="#0f4a6b"/>
    <circle cx="580" cy="230" r="110" fill="#2a8fd0"/>
    <circle cx="580" cy="230" r="103" fill="#ffffff"/>
    <rect y="340" width="560" height="33" fill="#0b2a3d"/>
  </svg>

  <p class="headline">
    “Business with no limits, meet mailing with no addresses, gain new customers through
    <span class="headline__program">“Open Porch Route Drop”</span>
    reach new customers at their home without needing their address.”
  </p>

  <ul class="specials">
    <li>Double your order FREE</li>
    <li class="note">(order 500 business cards and get 1000)</li>
    <li>250 100lb gloss stock brochures 99.00</li>
    <li>business packages</li>
    <li>(cards, envelopes and letterhead) 299</li>
    <li>1000 flyers 140.40</li>
    <li>5000 postcards 179.99</li>
  </ul>

  <div class="logo-badge">InkWillow</div>

  <div class="samples" role="img" aria-label="Collage of printed samples: letterhead, envelopes, flyers and brochures"></div>

  <p class="order-line">order 24/7 orders@inkwillow.com</p>
</section>

<section class="postcard postcard--back" aria-label="Postcard back">
  <svg class="postcard__art" viewBox="0 0 560 373" preserveAspectRatio="none" aria-hidden="true">
    <defs>
      <linearGradient id="back-sky" x1="0" y1="0" x2="0" y2="1">
        <stop offset="0" stop-color="#165f89"/>
        <stop offset=".45" stop-color="#2f9fd6"/>
        <stop offset="1" stop-color="#45b0e0"/>
      </linearGradient>
    </defs>
    <rect width="560" height="373" fill="url(#back-sky)"/>
    <path d="M560,160 C462,212 350,290 272,373 H560 Z" fill="#070707"/>
    <path d="M560,168 C466,220 356,296 280,373 H560 Z" fill="#3fae49"/>
    <path d="M560,176 C470,227 362,302 288,373 H560 Z" fill="#e8ee1c"/>
    <path d="M560,184 C474,234 368,308 296,373 H560 Z" fill="#2a8fd0"/>
    <path d="M560,194 C480,242 376,314 306,373 H560 Z" fill="#0b2a3d"/>
  </svg>

  <div class="services-label">Our Services Are</div>

  <ul class="services services--first">
    <li>banners</li>
    <li>booklets</li>
    <li>brochures</li>
    <li>business cards</li>
    <li>calendars</li>
    <li>catalogs</li>
  </ul>
  <ul class="services services--second">
    <li>CD/DVD packages</li>
    <li>envelopes</li>
    <li>event tickets</li>
    <li>flyers</li>
    <li>hangtags</li>
    <li>postcards</li>
  </ul>
  <ul class="services services--third">
    <li>posters</li>
    <li>presentation folders</li>
    <li>rack cards</li>
    <li>labels</li>
    <li>table tents</li>
    <li>window cling and decal</li>
  </ul>

  <div class="stamp-box">Postage<br>Stamp</div>

  <p class="order-line">order 24/7 orders@inkwillow.com</p>
</section>

</body>
</html>
```